Laboratory and geotechnical service provider needs Word template

We require a new Word Template for our business. We are looking for a modern, business-like format. We typically generate reports such as management plans, business plans, method statements, technical reports. These reports cover generally between 5 and 30 pages, but sometimes up to 500 pages including the appendices.

Lab reports have their own formats and are not parts of this scope.

Target Market(s)

We report to Clients such as construction industry contractors, governmental departments and engineering consultants.

Industry/Entity Type

Technical Service

Colors

Designer to choose colors to be used in the design.

Requirements
Must have
• The report needs a fancy cover page with a title field, subtitle, project field, client name field, reference number field. Photo/graphics as background on cover. Second page needs a revision table for document control. Table of contents up to 2 levels. Appendices to be part of TOC. Report first page with custom headings for body text, titles, subtitles, headings 1, 2, 3, etc. Include a table with caption, figure with caption, bullet list, numbered list. Appendix page. Please use fonts consistently, choose a common, but professional, modern font.
Nice to have
• We traditionally use black and yellow as company colours. Please visit our company page www.brennixtesting.com.
Should not have
• The two attached word documents is what we use now for your information, we are looking for something better!

```html
<!DOCTYPE html>
<html lang="en">
<head>
<meta charset="utf-8">
<title>Brennix Testing Co. WLL – Report Template</title>
<link href="https://fonts.googleapis.com/css2?family=Source+Sans+3:wght@300;400;700&display=swap" rel="stylesheet">
<style>
:root{
  --canvas:#FDC923;
  --yellow:#FFCF00;
  --black:#000;
  --gray:#4D4D4D;
  --mid:#8a8a8a;
  --light:#cfcfcf;
  --text:#3a3a3a;
  --white:#fff;
}
*{box-sizing:border-box;margin:0;padding:0}
html,body{width:1200px;height:849px;overflow:hidden}
body{background:var(--canvas);font-family:"Source Sans 3",sans-serif;color:var(--black);position:relative}

.brand{position:absolute;left:64px;top:20px;display:flex;align-items:center;gap:8px}
.brand-mark{width:72px;height:55px;border:2px solid var(--black);display:flex;align-items:center;justify-content:center;font-weight:700;font-size:15px}
.brand-name{font-size:20px;font-weight:400}

.page{position:absolute;width:228px;height:323px;background:var(--white);box-shadow:0 1px 3px rgba(0,0,0,.25);overflow:hidden}
.page-header{position:absolute;left:0;top:0;width:100%;height:27px;background:var(--yellow);border-bottom:1px solid var(--black)}
.page-header .company{position:absolute;left:11px;top:15px;font-size:4.2px}
.page-header .mark{position:absolute;right:11px;top:12px;font-size:5.5px;font-weight:700}
.page-footer{position:absolute;left:0;top:301px;width:100%;height:1.5px;background:var(--yellow)}
.page-number{position:absolute;right:22px;top:308px;font-size:4.2px}

.page-label{position:absolute;width:228px;text-align:center;font-size:11.5px}

.body-text{position:absolute;font-size:4.2px;line-height:5.5px;color:var(--text)}
.body-text p+p{margin-top:6px}
.band{position:absolute;left:0;width:100%;height:6px;background:var(--yellow);font-size:4.6px;font-weight:700;padding-left:22px;line-height:6px}

/* cover */
.cover-photo{position:absolute;left:0;top:0;width:100%;height:227px;background:linear-gradient(160deg,#f0cf10 0%,#c9a900 45%,#8a7400 100%)}
.cover-rule{position:absolute;left:0;top:227px;width:100%;height:2px;background:var(--black)}
.cover-title{position:absolute;right:45px;top:194px;text-align:right;color:var(--yellow);font-weight:700;font-size:12.5px;line-height:12px}
.cover-subtitle{display:block;color:var(--white);font-weight:400;font-size:6.3px;line-height:8px}
.cover-mark{position:absolute;left:187px;top:194px;width:31px;height:24px;background:var(--yellow);display:flex;align-items:center;justify-content:center;font-size:6px;font-weight:700}
.project-title{position:absolute;left:18px;top:236px;font-size:9.5px;font-weight:700}
.reference{position:absolute;left:18px;top:250px;font-size:5px;color:var(--text)}
.client-name{position:absolute;left:18px;top:266px;font-size:9.5px;color:var(--gray)}
.contacts{position:absolute;left:18px;top:290px;font-size:5px;line-height:7.6px;list-style:none}
.contacts li{display:flex;align-items:center;gap:4px}
.contacts svg{width:5px;height:5px}

/* tables */
table{position:absolute;border-collapse:collapse;font-size:4px;color:var(--text)}
td,th{border:0.5px solid var(--mid);height:8px;padding:0 1.5px;font-weight:400;text-align:center}
th{background:var(--gray);color:var(--white)}
.left{text-align:left}
.copy-box{position:absolute;left:130px;width:76px;height:7px;background:var(--light);font-size:4px;padding-left:3px;line-height:7px}

/* toc */
.toc{position:absolute;left:22px;top:53px;width:184px;list-style:none;font-size:3.9px;line-height:5.5px;color:var(--mid)}
.toc li{display:flex;justify-content:space-between}
.toc .sub{padding-left:14px}
.toc .gap{margin-top:5.5px}

.h2{position:absolute;left:22px;top:48px;font-size:5px;font-weight:700}
.h3{position:absolute;left:22px;top:60px;font-size:5px}
.para-label{position:absolute;left:22px;top:71px;font-size:4.2px}
.table-caption{position:absolute;left:22px;font-size:2.6px;font-style:italic;color:var(--mid)}
.total{background:var(--light);font-weight:700;color:var(--black)}

/* figure */
.figure{position:absolute;left:0;top:106px;width:100%;height:127px;background:linear-gradient(180deg,#d7dde3 0%,#b9c2cb 55%,#8f9aa4 100%)}
.figure-note{position:absolute;left:0;top:210px;width:100%;height:12px;background:rgba(40,40,40,.85);color:var(--yellow);font-size:6.3px;text-align:center;line-height:12px}

.list-title{position:absolute;left:22px;font-size:4.6px;font-weight:700}
.plain-list{position:absolute;left:22px;list-style:none;font-size:4px;line-height:5.5px;color:var(--text)}
.plain-list .sub{padding-left:14px}
.bullets li::before{content:"\25AA";margin-right:2px}

.type-panel{position:absolute;left:908px;top:538px}
.panel-title{font-size:21px;font-weight:700;line-height:26px}
.font-sample{font-size:16.5px;line-height:19px;white-space:nowrap}
.swatches{position:absolute;left:908px;top:702px;display:flex;gap:9px}
.swatch{width:50px;text-align:center;font-size:11px;line-height:13px;white-space:nowrap;display:flex;flex-direction:column;align-items:center}
.swatch span{display:block;width:50px;height:50px;border:3px solid var(--white);margin-bottom:3px}
</style>
</head>
<body>

<header class="brand">
  <div class="brand-mark">Brennix</div>
  <div class="brand-name">Brennix Testing Co. WLL</div>
</header>

<!-- Cover page -->
<section class="page" style="left:64px;top:97px">
  <div class="cover-photo" role="img" aria-label="Cover photograph: laboratory technician at a microscope with drilling rig and city skyline, tinted yellow"></div>
  <div class="cover-rule"></div>
  <div class="cover-title">Document Title<span class="cover-subtitle">Document Subtitle</span></div>
  <div class="cover-mark">Brennix</div>
  <div class="project-title">Project Title</div>
  <div class="reference">reference number</div>
  <div class="client-name">Clients Name</div>
  <ul class="contacts">
    <li><svg viewBox="0 0 10 10"><path d="M1 4h8l-1 5H2z M2 3c1-2 5-2 6 0" fill="#000"/></svg>+974 4012 5580</li>
    <li><svg viewBox="0 0 10 10"><text x="0" y="8.5" font-size="10" font-family="sans-serif">@</text></svg>info@brennixtesting.com</li>
    <li><svg viewBox="0 0 10 10"><rect x="0" y="2" width="10" height="7" fill="#000"/><rect x="2" y="4" width="6" height="3" fill="#fff"/></svg>www.brennixtesting.com</li>
  </ul>
</section>
<div class="page-label" style="left:64px;top:422px">Cover page</div>

<!-- Revision list -->
<section class="page" style="left:345px;top:97px">
  <div class="page-header"><span class="company">Brennix Testing Co. WLL</span><span class="mark">Brennix</span></div>
  <table style="left:21px;top:34px;width:185px">
    <tr><th style="width:12px">Rev</th><th style="width:28px">Date</th><th>Details</th><th style="width:25px">Prepared</th><th style="width:25px">Checked</th><th style="width:27px">Approved</th></tr>
    <tr><td colspan="6" style="border:none;height:3px"></td></tr>
    <tr><td>1</td><td>03.12.2019</td><td>1st draft</td><td>RSV</td><td>TV</td><td>AJS</td></tr>
    <tr><td>2</td><td>04.12.2019</td><td>2nd draft</td><td>RSV</td><td>TV</td><td>AJS</td></tr>
    <tr><td>3</td><td>05.12.2019</td><td>1st Issue</td><td>RSV</td><td>TV</td><td>AJS</td></tr>
  </table>
  <div class="copy-box" style="top:75px">Copy no. : 1/5</div>
  <div class="copy-box" style="top:83px">Controlled Copy : &nbsp;YES</div>
  <div class="page-footer"></div><div class="page-number">2</div>
</section>
<div class="page-label" style="left:345px;top:422px">Revision list</div>

<!-- Table of contents -->
<section class="page" style="left:627px;top:97px">
  <div class="page-header"><span class="company">Brennix Testing Co. WLL</span><span class="mark">Brennix</span></div>
  <div class="band" style="top:39px">Table of contents</div>
  <ul class="toc">
    <li><span>1 Introduction</span><span>3</span></li>
    <li><span>2 Project overview</span><span>4</span></li>
    <li class="sub"><span>2.1 Under segment 1</span><span>4</span></li>
    <li class="sub"><span>2.2 Under segment 2</span><span>5</span></li>
    <li class="sub"><span>2.3 Under segment 3</span><span>6</span></li>
    <li><span>3 Technical requirements</span><span>8</span></li>
    <li class="sub"><span>3.1 Under segment 1</span><span>11</span></li>
    <li class="sub"><span>3.2 Under segment 2</span><span>13</span></li>
    <li class="sub"><span>3.3 Under segment 3</span><span>15</span></li>
    <li class="sub"><span>3.4 Under segment 4</span><span>18</span></li>
    <li class="sub"><span>3.5 Under segment 5</span><span>23</span></li>
    <li class="sub"><span>3.6 Under segment 6</span><span>29</span></li>
    <li><span>4 Business Management Requirement</span><span>32</span></li>
    <li class="sub"><span>4.1 Under segment 1</span><span>31</span></li>
    <li class="sub"><span>4.2 Under segment 2</span><span>38</span></li>
    <li class="sub"><span>4.3 Under segment 3</span><span>41</span></li>
    <li class="gap"><span>Appendix A</span><span>42</span></li>
    <li class="sub"><span>Appendix A – Undersegment 1</span><span>43</span></li>
    <li><span>Appendix B</span><span>44</span></li>
    <li><span>Appendix C</span><span>48</span></li>
  </ul>
  <div class="page-footer"></div><div class="page-number">3</div>
</section>
<div class="page-label" style="left:627px;top:422px">Table of contents</div>

<!-- Headings + paragraph + tables -->
<section class="page" style="left:908px;top:97px">
  <div class="page-header"><span class="company">Brennix Testing Co. WLL</span><span class="mark">Brennix</span></div>
  <div class="band" style="top:38px">1. Heading 1</div>
  <div class="h2">1.1 Heading 2</div>
  <div class="h3">1.11 Heading 3</div>
  <div class="para-label">Paragraph</div>
  <div class="body-text" style="left:22px;top:83px;width:184px">
    <p>At vero eos et accusamus et iusto odio dignissimos ducimus qui blanditiis praesentium voluptatum deleniti atque corrupti quos dolores et quas molestias excepturi sint occaecati cupiditate non provident, similique sunt in culpa qui officia deserunt mollitia animi, id est laborum et dolorum fuga. Et harum quidem rerum facilis est et expedita distinctio. Nam libero tempore, cum soluta nobis est eligendi optio cumque nihil impedit quo minus id quod maxime placeat facere possimus, omnis voluptas assumenda est, omnis dolor repellendus. Temporibus autem quibusdam et aut officiis debitis aut rerum necessitatibus saepe eveniet ut et voluptates repudiandae sint et molestiae non recusandae. Itaque earum rerum hic tenetur a sapiente delectus, ut aut reiciendis voluptatibus maiores alias consequatur aut perferendis doloribus asperiores repellat.</p>
  </div>
  <table style="left:22px;top:149px;width:185px">
    <tr><th class="left" colspan="2">No. &nbsp;Title 1</th><th class="left" style="width:24px">Title 2</th><th class="left" style="width:25px">Title 3</th><th class="left" style="width:59px">Title 4</th></tr>
    <tr><td style="width:10px">1</td><td class="left">Content</td><td class="left">Content</td><td class="left">Content</td><td class="left">Content</td></tr>
    <tr><td>2</td><td class="left">Content</td><td class="left">Content</td><td class="left">Content</td><td class="left">Content</td></tr>
    <tr><td>3</td><td class="left">Content</td><td class="left">Content</td><td class="left">Content</td><td class="left">Content</td></tr>
    <tr><td style="border:none"></td><td class="left" style="background:var(--light)">Conclusion / Total / Sum</td><td style="background:var(--light)"></td><td class="left">Pre Total</td><td class="left total">Total sum</td></tr>
  </table>
  <table style="left:148px;top:193px;width:59px"><tr><td class="left total">Total sum</td></tr></table>
  <div class="table-caption" style="top:201px">Caption text for table style 1</div>
  <table style="left:22px;top:210px;width:101px">
    <tr><th class="left" style="width:55px">List item 1</th><td style="width:23px">Text 01</td><td>01</td></tr>
    <tr><th class="left">List item 2</th><td>Text 02</td><td>02</td></tr>
    <tr><th class="left">List item 3</th><td>Text 03</td><td>03</td></tr>
    <tr><th class="left">List item 4</th><td>Text 04</td><td>04</td></tr>
    <tr><th class="left">List item 5</th><td>Text 05</td><td>05</td></tr>
    <tr><td colspan="3" style="border:none;height:3px"></td></tr>
    <tr><td style="border:none"></td><td class="total">Total</td><td class="total">Value</td></tr>
  </table>
  <div class="table-caption" style="top:262px">Caption text for table style 2</div>
  <div class="page-footer"></div><div class="page-number">4</div>
</section>
<div class="page-label" style="left:908px;top:422px;width:228px">Headings + Paragraph + Tables</div>

<!-- Paragraph & image -->
<section class="page" style="left:64px;top:473px">
  <div class="page-header"><span class="company">Brennix Testing Co. WLL</span><span class="mark">Brennix</span></div>
  <div class="body-text" style="left:22px;top:34px;width:186px">
    <p>Nam aliquet bibendum elit, ac imperdiet leo tristique sit amet. Pellentesque habitant morbi tristique senectus et netus et malesuada fames ac turpis egestas. Duis non scelerisque nunc. Donec luctus sollicitudin libero, eu condimentum ex tempor sit amet. Phasellus vel fringilla dui.</p>
    <p>&nbsp;&nbsp;&nbsp;&nbsp;&nbsp;&nbsp;Vivamus a dapibus neque. Interdum et malesuada fames ac ante ipsum primis in faucibus. Fusce quis viverra ligula, a egestas elit. Integer ut luctus lacus. Nunc et pretium sem. Nulla varius lacus et ligula sollicitudin, vel tempor urna tincidunt. Nam et nulla pretium, rutrum mi nec, laoreet odio. Fusce scelerisque malesuada odio, et auctor enim lacinia vel. Maecenas quis augue id erat cursus lacinia vel ut lectus. In elementum efficitur libero, a eleifend mauris dictum eget. Sed ut varius lacus, vitae pulvinar metus. Nullam eu turpis sit amet augue volutpat faucibus.</p>
  </div>
  <div class="figure" role="img" aria-label="Photograph: wide laboratory hall with technicians in yellow coats working at benches"></div>
  <div class="figure-note">&#8592; Images if possible should always be from edge to edge. &#8594;</div>
  <div class="table-caption" style="top:230px">Caption text for figure style 1</div>
  <div class="body-text" style="left:22px;top:239px;width:186px">
    <p>Sed ut perspiciatis unde omnis iste natus error sit voluptatem accusantium doloremque laudantium, totam rem aperiam, eaque ipsa quae ab illo inventore veritatis et quasi architecto beatae vitae dicta sunt explicabo. Nemo enim ipsam voluptatem quia voluptas sit aspernatur aut odit aut fugit, sed quia consequuntur magni dolores eos qui ratione voluptatem sequi nesciunt. Neque porro quisquam est, qui dolorem ipsum quia dolor sit amet, consectetur, adipisci velit, sed quia non numquam eius modi tempora incidunt ut labore et dolore magnam aliquam quaerat voluptatem. Ut enim ad minima veniam, quis nostrum exercitationem ullam corporis suscipit laboriosam, nisi ut aliquid ex ea commodi consequatur?</p>
  </div>
  <div class="page-footer"></div><div class="page-number">5</div>
</section>
<div class="page-label" style="left:64px;top:798px">Parapgraph &amp; Image</div>

<!-- Numbered & bulleted lists -->
<section class="page" style="left:345px;top:473px">
  <div class="page-header"><span class="company">Brennix Testing Co. WLL</span><span class="mark">Brennix</span></div>
  <div class="body-text" style="left:22px;top:34px;width:186px">
    <p>Nullam fermentum, dolor quis iaculis maximus, sem erat auctor orci, a dignissim arcu nisi quis nunc. Sed eu sem at velit tempor finibus eget non felis. Vivamus lacus dolor, porta vitae orci vitae, auctor commodo nisl. Vestibulum luctus odio ex, nec pulvinar orci tincidunt at. Suspendisse potenti. Curabitur ornare nibh porttitor augue porta, eget consequat augue cursus.</p>
  </div>
  <div class="list-title" style="top:68px">List with numbers:</div>
  <ul class="plain-list" style="top:75px">
    <li>1 Text enumeration</li><li>2 Text enumeration</li><li>3 Text enumeration</li><li>4 Text enumeration</li><li>5 Text enumeration</li><li>6 Text enumeration</li>
    <li class="sub">6.1 Subnumeration if needed</li><li class="sub">6.2 Subnumeration if needed</li>
    <li>7 Text enumeration</li><li>8 Text enumeration</li><li>9 Text enumeration</li><li>10 Text enumeration</li><li>11 Text enumeration</li><li>12 Text enumeration</li><li>13 Text enumeration</li><li>14 Text enumeration</li>
  </ul>
  <div class="body-text" style="left:22px;top:166px;width:186px">
    <p>Mauris et turpis molestie, tempus sem vel, pretium justo. Vivamus urna erat, pulvinar fringilla est ac, fringilla ullamcorper sem. Curabitur venenatis sit amet diam eu condimentum. Sed rutrum vehicula massa. Fusce nibh lectus, rhoncus nec arcu a, vulputate tempor nibh.</p>
  </div>
  <div class="list-title" style="top:196px">List with bullets:</div>
  <ul class="plain-list bullets" style="top:203px">
    <li>Bullet text</li><li>Bullet text</li><li>Bullet text</li><li>Bullet text</li><li>Bullet text</li><li>Bullet text</li><li>Bullet text</li><li>Bullet text</li><li>Bullet text</li>
  </ul>
  <div class="body-text" style="left:22px;top:257px;width:186px">
    <p>Nunc in vulputate magna. Donec quis libero ut massa vulputate bibendum. Curabitur sodales, quam in vestibulum consectetur, ex neque varius elit, eget viverra nunc metus nec sem. Praesent semper nec magna dignissim tempor. Etiam vitae vehicula tellus. Nullam augue ligula, elementum non tellus ut, vestibulum imperdiet justo. Fusce sed nisl cursus, ultrices arcu eget, sagittis ante.</p>
  </div>
  <div class="page-footer"></div><div class="page-number">6</div>
</section>
<div class="page-label" style="left:345px;top:798px">Numbered &amp; Bulleted lists</div>

<!-- Appendix page -->
<section class="page" style="left:627px;top:473px">
  <div class="page-header"><span class="company">Brennix Testing Co. WLL</span><span class="mark">Brennix</span></div>
  <div class="band" style="top:39px">Appendix 1</div>
  <div class="body-text" style="left:22px;top:56px;width:184px">
    <p>Nemo enim ipsam voluptatem quia voluptas sit aspernatur aut odit aut fugit, sed quia consequuntur magni dolores eos qui ratione voluptatem sequi nesciunt. Neque porro quisquam est, qui dolorem ipsum quia dolor sit amet, consectetur, adipisci velit, sed quia non numquam eius modi tempora incidunt ut labore et dolore magnam aliquam quaerat voluptatem. Ut enim ad minima veniam, quis nostrum exercitationem ullam corporis suscipit laboriosam, nisi ut aliquid ex ea commodi consequatur?</p>
  </div>
  <div class="page-footer"></div><div class="page-number">7</div>
</section>
<div class="page-label" style="left:627px;top:798px">Appendix page</div>

<!-- Type & colour specification -->
<div class="type-panel">
  <div class="panel-title">Fonts used :</div>
  <div style="height:14px"></div>
  <div class="font-sample" style="font-weight:400">Vantor Sans - Regular</div>
  <div class="font-sample" style="font-weight:700">Vantor Sans - Bold</div>
  <div class="font-sample" style="font-weight:300">Vantor Sans - Light</div>
  <div style="height:16px"></div>
  <div class="panel-title">Colors used :</div>
</div>
<div class="swatches">
  <div class="swatch"><span style="background:var(--black)"></span>Black</div>
  <div class="swatch"><span style="background:var(--gray)"></span>Dark gray 1</div>
  <div class="swatch"><span style="background:var(--yellow)"></span>Yellow<br>#FFCF00</div>
</div>

</body>
</html>
```